Trading company needs a non alcoholic beer Can design

We KLW are trading company , food Distributors in Africa -RD Congo/Kinshasa .We want to do a Private label non alcoholic beer 500ml can and need a design for this Project .
the Brand Name is : RIVO BREW
We want it to be similar NOT a copy of Velmont 0.0% can ( picture
attached ) as we want to respect the intellectual properties .so we prefer to use the same colors but more elegant ,modern style .
thanks.
THE DESIGN MUST STATE ITS A NON ALCOHOLIC BEER
PLZ SEARCH FOR VELMONT 0.0% MALT DRINK YOU WILL FIND 2 DESIGNS OLD AND NEW WE NEED SOMTHING SIMILAR TO THESE DESIGNS ,KINDLY USE SAME COLORS AND THE 0.0% SHOULD BE IN THE MIDDLE OF THE CAN .
Target Market(s)
THE PRODUCT WILL BE SOLD IN THE SUPERMASRKTS / MODERN TRADE
Look and feel

```html
<!DOCTYPE html>
<html lang="en">
<head>
<meta charset="utf-8">
<title>RIVO BREW 0.0% – Can Label</title>
<link rel="stylesheet" href="https://fonts.googleapis.com/css2?family=Fira+Sans+Extra+Condensed:wght@700;800&family=Oswald:wght@300;600&display=swap">
<style>
  :root {
    --bg: #f4f4f2;
    --red-light: #e0584c;
    --red-deep: #c2131a;
    --red-right: #c62b26;
    --blue-light: #4a72b0;
    --blue-deep: #15307f;
    --gold: #b39a4a;
    --cream: #e8e2d8;
    --silver-dark: #9ea4a8;
    --silver-light: #eef2f4;
    --silver-blue: #d3e3ec;
  }
  html, body {
    margin: 0;
    padding: 0;
    overflow: hidden;
    background: var(--bg);
  }
  .canvas {
    position: relative;
    width: 900px;
    height: 1200px;
    overflow: hidden;
    background: var(--bg);
  }
  .label {
    position: absolute;
    left: 180px;
    top: 20px;
    width: 540px;
    height: 1160px;
    display: block;
  }
  .brand-name {
    font-family: "Oswald", sans-serif;
    font-weight: 600;
    font-size: 74px;
    fill: var(--cream);
    letter-spacing: 1px;
  }
  .tagline {
    font-family: "Fira Sans Extra Condensed", sans-serif;
    font-weight: 700;
    font-size: 60px;
    fill: var(--cream);
  }
  .abv {
    font-family: "Fira Sans Extra Condensed", sans-serif;
    font-weight: 800;
    fill: var(--cream);
    stroke: var(--gold);
    stroke-width: 4px;
    paint-order: stroke;
  }
  .abv-unit {
    font-family: "Fira Sans Extra Condensed", sans-serif;
    font-weight: 800;
    font-size: 22px;
    fill: var(--cream);
  }
  .info {
    font-family: "Oswald", sans-serif;
    font-weight: 300;
    font-size: 34px;
    fill: var(--cream);
  }
</style>
</head>
<body>
<div class="canvas">
  <svg class="label" viewBox="0 0 540 1160" xmlns="http://www.w3.org/2000/svg">
    <defs>
      <linearGradient id="silverSide" x1="0" y1="0" x2="0" y2="1">
        <stop offset="0" stop-color="var(--silver-dark)"/>
        <stop offset="0.25" stop-color="var(--silver-light)"/>
        <stop offset="0.5" stop-color="var(--silver-blue)"/>
        <stop offset="0.75" stop-color="var(--silver-light)"/>
        <stop offset="1" stop-color="var(--silver-dark)"/>
      </linearGradient>
      <linearGradient id="redBand" x1="0" y1="0" x2="1" y2="0">
        <stop offset="0" stop-color="var(--red-light)"/>
        <stop offset="0.55" stop-color="var(--red-deep)"/>
        <stop offset="1" stop-color="var(--red-right)"/>
      </linearGradient>
      <linearGradient id="blueBand" x1="0" y1="0" x2="1" y2="0">
        <stop offset="0" stop-color="var(--blue-light)"/>
        <stop offset="1" stop-color="var(--blue-deep)"/>
      </linearGradient>
      <clipPath id="centerClip">
        <rect x="88" y="0" width="366" height="1160"/>
      </clipPath>
    </defs>

    <!-- metal side panels -->
    <rect class="side-panel" x="0" y="0" width="88" height="1160" fill="url(#silverSide)" role="img" aria-label="Silver diamond-plate metal texture"/>
    <rect class="side-panel" x="454" y="0" width="86" height="1160" fill="url(#silverSide)" role="img" aria-label="Silver diamond-plate metal texture"/>

    <!-- central red band -->
    <rect class="center-band" x="88" y="0" width="366" height="1160" fill="url(#redBand)"/>

    <!-- gem emblem area -->
    <rect class="gem" x="217" y="65" width="108" height="78" rx="6" fill="#d7dde2" role="img" aria-label="Faceted diamond illustration"/>

    <!-- brand name -->
    <text class="brand-name" x="271" y="285" text-anchor="middle">RIVO BREW</text>

    <!-- small star ornament area -->
    <rect class="star" x="253" y="356" width="36" height="36" rx="4" fill="#d8cfae" role="img" aria-label="Small gold star ornament"/>

    <g clip-path="url(#centerClip)">
      <!-- tagline -->
      <g transform="translate(271,490) rotate(-21.5)">
        <text class="tagline" x="-28" y="-16" text-anchor="middle">PREMIUM</text>
        <text class="tagline" x="33" y="53" text-anchor="middle">ORIGINAL</text>
      </g>

      <!-- diagonal blue band -->
      <polygon class="abv-band" points="88,648 454,504 454,785 88,943" fill="url(#blueBand)"/>
      <line x1="88" y1="648" x2="454" y2="504" stroke="var(--gold)" stroke-width="5"/>
      <line x1="88" y1="943" x2="454" y2="785" stroke="var(--gold)" stroke-width="5"/>

      <!-- alcohol content -->
      <g transform="translate(248,727) rotate(-21.5)">
        <text class="abv" x="-20" y="85" text-anchor="middle" font-size="230">0.0</text>
        <text class="abv" x="172" y="-30" text-anchor="middle" font-size="110">%</text>
        <text class="abv-unit" x="150" y="70" text-anchor="middle">ALC.</text>
      </g>
    </g>

    <!-- product information -->
    <text class="info" x="271" y="984" text-anchor="middle">NON ALCOHOLIC</text>
    <text class="info" x="271" y="1034" text-anchor="middle">MALT DRINKS</text>
    <text class="info" x="271" y="1092" text-anchor="middle">500ml</text>
  </svg>
</div>
</body>
</html>
```